KAJU Freightways #ALLKAJU Business Cards & Letterhead

I am looking to business cards designed for our organization. We are currently undergoing a small re-branding that is taking place. Our organization is called KAJU Freightways and we are headquartered in Phoenix, AZ. We primarily provide transportation and logistics services to the Marlow Parcel Bureau who is our largest customer. I would like to see a design that incorporates name, title, contact info, website, and address (this will be different depending on the employee). I would also like to see some color on the business card using our logo colors or a variation. I would like our logo on the back of the business card with the website displayed. The final design should communicate that we are a next generation transportation operate that focuses on being driver-first, customer-centric, innovative, and sustainable.We would also like our #ALLKAJU catch phrase incorporated as well.

Target Market(s)

Transportation & Logistics

Industry/Entity Type

Trucking Company

Contact Information for Business Card

-First and Last Name
-Position Title
-Contact Phone
-Contact Email
-Physical Address

Font styles to use
Serif

Colors

Designer to choose colors to be used in the design.

Requirements
Must have
• -KAJU logo prominently displayed
• -#ALLKAJU catch phrase used
• -Some amount of color, design gradient, etc.
• -Logo on the back with website listed (https://www.kajufreightco.example)

```html
<!DOCTYPE html>
<html lang="en">
<head>
<meta charset="utf-8">
<title>KAJU Freightways Business Card</title>
<link href="https://fonts.googleapis.com/css2?family=Roboto+Slab:wght@300;400;500;800&display=swap" rel="stylesheet">
<style>
  :root {
    --backdrop: #e9ecef;
    --card: #ffffff;
    --brand-green: #6cb33e;
    --brand-navy: #0b2a35;
    --ink: #1f3540;
    --ring: #ffffff;
  }
  html, body {
    margin: 0;
    padding: 0;
    width: 1200px;
    height: 900px;
    overflow: hidden;
    background: var(--backdrop);
    font-family: "Roboto Slab", Georgia, serif;
  }
  .business-card {
    position: absolute;
    left: 280px;
    top: 203px;
    width: 750px;
    height: 428px;
    background: var(--card);
    overflow: hidden;
    box-shadow: 0 10px 30px rgba(0, 0, 0, 0.12);
  }
  .brand-panel {
    position: absolute;
    inset: 0;
    width: 750px;
    height: 428px;
  }
  .logo-word {
    font-family: "Roboto Slab", Georgia, serif;
    font-weight: 800;
    font-size: 104px;
    fill: var(--card);
  }
  .catch-phrase {
    font-family: "Roboto Slab", Georgia, serif;
    font-weight: 500;
    font-size: 22px;
    letter-spacing: 3px;
    fill: var(--brand-green);
  }
  .identity {
    position: absolute;
    left: 46px;
    top: 62px;
  }
  .person-name {
    margin: 0;
    font-size: 25px;
    font-weight: 500;
    color: var(--brand-green);
    line-height: 1.2;
  }
  .person-title {
    margin: 2px 0 0;
    font-size: 17px;
    font-weight: 400;
    color: var(--ink);
  }
  .contact-list {
    position: absolute;
    left: 46px;
    top: 178px;
    margin: 0;
    padding: 0;
    list-style: none;
  }
  .contact-item {
    display: flex;
    align-items: center;
    height: 23.5px;
    font-size: 15.5px;
    font-weight: 300;
    color: var(--ink);
  }
  .contact-icon {
    width: 15px;
    height: 15px;
    margin-right: 11px;
    fill: var(--brand-green);
  }
  .address {
    position: absolute;
    left: 46px;
    top: 316px;
    margin: 0;
    font-style: normal;
    font-size: 15.5px;
    font-weight: 300;
    line-height: 22px;
    color: var(--ink);
  }
</style>
</head>
<body>
  <section class="business-card">
    <svg class="brand-panel" viewBox="0 0 750 428" aria-hidden="true">
      <rect x="580" y="0" width="170" height="428" fill="var(--brand-green)"/>
      <circle cx="533" cy="215" r="219" fill="var(--ring)"/>
      <circle cx="533" cy="215" r="205" fill="var(--brand-navy)"/>
      <text class="logo-word" x="533" y="250" text-anchor="middle" textLength="320" lengthAdjust="spacingAndGlyphs">KAJU</text>
      <text class="catch-phrase" x="533" y="312" text-anchor="middle">#ALLKAJU</text>
    </svg>

    <div class="identity">
      <h1 class="person-name">Dana Whitfield</h1>
      <p class="person-title">Manager</p>
    </div>

    <ul class="contact-list">
      <li class="contact-item">
        <svg class="contact-icon" viewBox="0 0 24 24" aria-hidden="true"><path d="M6.6 10.8a15.1 15.1 0 0 0 6.6 6.6l2.2-2.2a1 1 0 0 1 1-.25 11.4 11.4 0 0 0 3.6.57 1 1 0 0 1 1 1V20a1 1 0 0 1-1 1A17 17 0 0 1 3 4a1 1 0 0 1 1-1h3.5a1 1 0 0 1 1 1c0 1.25.2 2.45.57 3.57a1 1 0 0 1-.25 1z"/></svg>
        480-555-0142
      </li>
      <li class="contact-item">
        <svg class="contact-icon" viewBox="0 0 24 24" aria-hidden="true"><path d="M2 5h20v14H2z"/><path d="M2 5l10 8 10-8" stroke="#fff" stroke-width="1.5" fill="none"/></svg>
        info@kajufreightco.example
      </li>
      <li class="contact-item">
        <svg class="contact-icon" viewBox="0 0 24 24" aria-hidden="true"><circle cx="12" cy="12" r="10"/><path d="M2 12h20M12 2c3 3 3 17 0 20M12 2c-3 3-3 17 0 20" stroke="#fff" stroke-width="1.5" fill="none"/></svg>
        www.kajufreightco.example
      </li>
    </ul>

    <address class="address">
      1470 North Saguaro Ridge Road<br>
      Phoenix, AZ 85027
    </address>
  </section>
</body>
</html>
```